Travel Agency Website - Simple General

Need a 7 page simple design that is pretty repetitive. Need to be able to load quickly that is SEO optimized. Trying to give ideas on what they can do, be personal as we are local, but at the same time come across as professional and get information easily with little burden.

- Landing Page
- Brimwell Vacations Page
- Family Trips
- Road Trips from Texas
- Other Destinations
- About Us Page
- Contact Us Page

Target Market(s)

Families

Coding

Coded - Design and coding required

Number of Pages Required

5+ page

Colors

Designer to choose colors to be used in the design.

Requirements
Must have
• Like it to flow easily with our logo. Use that for colors, etc.

```html
<!DOCTYPE html>
<html lang="en">
<head>
<meta charset="utf-8">
<title>Roam Along Road – Travel Co.</title>
<link rel="stylesheet" href="https://fonts.googleapis.com/css2?family=Inter:wght@400;500;600;700;800&display=swap">
<style>
  :root {
    --sky-top: #0a9fd3;
    --sky-mid: #2cb3e0;
    --sky-low: #8fd6ef;
    --teal-deep: #1a4d5c;
    --teal-text: #1a5c6b;
    --accent-cyan: #12c3f2;
    --ink: #1d1d1d;
    --body-text: #333a3f;
    --muted: #5d6469;
    --icon-grey: #7a7f83;
    --pill-bg: #f1fbfd;
    --pill-border: #c9ecf3;
    --rule: #e2e4e6;
    --white: #ffffff;
  }
  * { box-sizing: border-box; margin: 0; padding: 0; }
  html, body { width: 695px; height: 1200px; overflow: hidden; background: var(--white); }
  body { position: relative; font-family: "Inter", Arial, sans-serif; color: var(--body-text); }
  .abs { position: absolute; }

  .top-stripe { left: 0; top: 0; width: 695px; height: 4px; background: #39c0ea; }

  .hero { left: 0; top: 4px; width: 695px; height: 428px;
    background:
      radial-gradient(ellipse 300px 90px at 50% 100%, rgba(70,140,165,.55) 0%, rgba(70,140,165,0) 100%),
      radial-gradient(ellipse at 50% 45%, #d9f1fa 0%, var(--sky-low) 25%, var(--sky-mid) 55%, var(--sky-top) 100%); }

  .brand { left: 20px; top: 22px; display: flex; align-items: center; gap: 5px; }
  .brand-dot { width: 10px; height: 10px; border-radius: 50%; background: var(--white); }
  .brand-name { font-size: 10px; font-weight: 700; color: var(--white); letter-spacing: .2px; }

  .main-nav { left: 0; top: 34px; width: 695px; height: 12px; }
  .main-nav a { position: absolute; top: 0; font-size: 7.7px; color: var(--white); text-decoration: none; white-space: nowrap; }
  .main-nav a.is-current { color: var(--teal-deep); font-weight: 500; }
  .main-nav a.is-current::before { content: ""; position: absolute; left: 0; right: 0; top: -4px; height: 1px; background: var(--teal-deep); }

  .slide-arrow { top: 200px; width: 22px; height: 22px; }

  .hero-caption { left: 151px; top: 251px; width: 377px; height: 87px; background: rgba(60,60,60,.62); text-align: center; }
  .hero-title { position: absolute; left: 0; right: 0; top: 17px; font-size: 19.5px; font-weight: 400; color: var(--white); }
  .hero-sub { position: absolute; left: 16px; top: 44px; font-size: 19px; color: var(--white); white-space: nowrap; }
  .hero-sub strong { font-size: 23px; font-weight: 800; color: var(--accent-cyan); margin-left: 6px; }

  .hero-wave { left: 0; top: 340px; width: 695px; height: 92px; }

  .tagline-pill { left: 256px; top: 447px; width: 183px; height: 19px; background: var(--pill-bg); border: 1px solid var(--pill-border);
    border-radius: 2px; font-size: 8.7px; font-weight: 500; color: var(--teal-text); text-align: center; line-height: 17px; }

  .intro { left: 88px; width: 525px; font-size: 7.3px; line-height: 11.6px; color: var(--body-text); }
  .intro strong { color: #000; font-weight: 600; }

  .card-title { font-size: 9.7px; font-weight: 500; color: var(--teal-text); white-space: nowrap; }
  .card-partner { font-size: 6.8px; font-weight: 500; color: var(--teal-text); white-space: nowrap; }
  .card-text { font-size: 7.3px; line-height: 9.4px; color: var(--body-text); }

  .card-photo { border-radius: 5px; overflow: hidden; }
  .photo-park { background: linear-gradient(#4a90e8 0%, #6fb0ee 35%, #3f7a4a 65%, #8c8f96 100%); }
  .photo-family { background: linear-gradient(120deg, #e9f1ee 0%, #a8c9b0 40%, #3b8f9e 70%, #c14a4a 100%); }
  .photo-city { background: linear-gradient(#5f8fbf 0%, #f1c48e 28%, #9a8c80 55%, #4d5660 100%); }
  .photo-getaway { background: linear-gradient(160deg, #7fc2f2 0%, #9ecff3 45%, #c9a36a 70%, #b3253a 100%); }
  .view-more { position: absolute; left: 0; bottom: 0; width: 100%; height: 31px; background: rgba(30,50,65,.62);
    color: var(--white); font-size: 8.7px; text-align: center; line-height: 31px; }
  .view-more svg { vertical-align: -1px; margin-left: 4px; }

  .footer-rule { left: 0; top: 1092px; width: 695px; height: 1px; background: var(--rule); }
  .footer-brand { left: 20px; top: 1128px; display: flex; align-items: center; gap: 5px; }
  .footer-brand .brand-dot { background: var(--teal-text); }
  .footer-brand .brand-name { color: var(--teal-text); font-size: 9px; }
  .footer-col a, .footer-col span { position: absolute; left: 0; font-size: 7.7px; color: var(--muted); text-decoration: none; white-space: nowrap; }
  .social { top: 1140px; width: 11.6px; height: 11.6px; border-radius: 3px; background: var(--icon-grey); }
  .bottom-bar { left: 0; top: 1196px; width: 695px; height: 4px; background: #d6d8da; }
</style>
</head>
<body>
  <div class="abs top-stripe"></div>

  <header>
    <div class="abs hero" role="img" aria-label="Cheerful traveller sitting on a suitcase atop the globe, surrounded by world landmarks, birds and a plane in a blue sky"></div>

    <div class="abs brand"><span class="brand-dot"></span><span class="brand-name">Roam Along Road</span></div>

    <nav class="abs main-nav">
      <a class="is-current" style="left:206px" href="#">Home</a>
      <a style="left:245px" href="#">Brimwell Vacations</a>
      <a style="left:327px" href="#">Family Trips</a>
      <a style="left:390px" href="#">Road Trips from Texas</a>
      <a style="left:491px" href="#">Other Destinations</a>
      <a style="left:579px" href="#">About Us</a>
      <a style="left:633px" href="#">Contact Us</a>
    </nav>

    <svg class="abs slide-arrow" style="left:23px" viewBox="0 0 22 22" aria-label="Previous slide">
      <circle cx="11" cy="11" r="9.8" fill="none" stroke="#fff" stroke-width="1.4" opacity=".8"/>
      <path d="M15.5 11H7M10.5 7.3 6.8 11l3.7 3.7" fill="none" stroke="#fff" stroke-width="1.4" opacity=".8"/>
    </svg>
    <svg class="abs slide-arrow" style="left:649px" viewBox="0 0 22 22" aria-label="Next slide">
      <circle cx="11" cy="11" r="9.8" fill="none" stroke="#fff" stroke-width="1.4" opacity=".8"/>
      <path d="M6.5 11H15M11.5 7.3 15.2 11l-3.7 3.7" fill="none" stroke="#fff" stroke-width="1.4" opacity=".8"/>
    </svg>

    <div class="abs hero-caption">
      <h1 class="hero-title">Roam Along Road</h1>
      <p class="hero-sub">Your local Guide to <strong>Big Adventure</strong></p>
    </div>

    <svg class="abs hero-wave" viewBox="0 340 695 92" preserveAspectRatio="none" aria-hidden="true">
      <path d="M0 402 Q90 382 200 370 Q347 352 500 362 Q620 372 695 400 L695 432 L0 432 Z" fill="var(--teal-deep)"/>
      <path d="M0 410 Q60 390 150 382 Q347 368 520 385 Q630 397 695 430 L695 432 L0 432 Z" fill="var(--white)"/>
    </svg>
  </header>

  <main>
    <p class="abs tagline-pill">No stress. No confusion. Just smooth</p>

    <p class="abs intro" style="top:478px">Turn your travel dreams into seamless, unforgettable experiences. At <strong>Roam Along Road</strong>, we believe planning your trip should feel just as exciting as the journey itself not overwhelming.</p>
    <p class="abs intro" style="top:512px">From magical theme park adventures and relaxing beach escapes to scenic road trips and hidden destination gems, we take care of every detail so you can focus on making memories. Whether you're traveling with family, friends, or planning a solo escape, we create personalized itineraries tailored to your style, budget, and pace.</p>
    <p class="abs intro" style="top:558px"><strong>No stress. No confusion. Just smooth</strong>, well-planned travel from start to finish.</p>

    <section>
      <h2 class="abs card-title" style="left:88px;top:595px">Brimwell Vacations – Land and Sea</h2>
      <p class="abs card-text" style="left:88px;top:610px;width:240px">Experience the magic on land and cruise the seas with perfectly planned Brimwell adventures.</p>
      <div class="abs card-photo photo-park" style="left:88px;top:638px;width:256px;height:169px" role="img" aria-label="Crowd at the gates of a theme park under a blue sky">
        <div class="view-more">View more<svg width="5" height="7" viewBox="0 0 5 7"><path d="M0 0 5 3.5 0 7Z" fill="#fff"/></svg></div>
      </div>
    </section>

    <section>
      <h2 class="abs card-title" style="left:360px;top:595px">Family Trips</h2>
      <p class="abs card-text" style="left:360px;top:610px;width:256px">Create lifelong memories with customized trips designed for all ages.</p>
      <div class="abs card-photo photo-family" style="left:359px;top:639px;width:255px;height:170px" role="img" aria-label="Family with suitcases walking past a fountain at a sunny resort"></div>
    </section>

    <section>
      <h2 class="abs card-title" style="left:88px;top:838px">Texas Road Trips</h2>
      <p class="abs card-partner" style="left:88px;top:851px">(Partnership with Lone Pine Van Rentals)</p>
      <p class="abs card-text" style="left:88px;top:863px;width:252px">Hit the road and explore Texas with flexible, fun, and comfortable van travel.</p>
      <div class="abs card-photo photo-city" style="left:88px;top:891px;width:256px;height:171px" role="img" aria-label="Aerial view of a Texas city skyline and highways at sunset"></div>
    </section>

    <section>
      <h2 class="abs card-title" style="left:359px;top:838px">Other Destinations</h2>
      <p class="abs card-text" style="left:359px;top:853px;width:225px">Discover unique destinations worldwide tailored to your travel dreams.</p>
      <div class="abs card-photo photo-getaway" style="left:359px;top:891px;width:255px;height:171px" role="img" aria-label="Hand holding a red suitcase with a straw hat, palm trees and a plane in the sky"></div>
    </section>
  </main>

  <footer>
    <div class="abs footer-rule"></div>
    <div class="abs footer-brand"><span class="brand-dot"></span><span class="brand-name">Roam Along Road</span></div>

    <div class="abs footer-col" style="left:144px;top:1109px">
      <a style="top:0" href="#">Home</a>
      <a style="top:16.5px" href="#">About Us</a>
      <a style="top:33px" href="#">Contact Us</a>
    </div>
    <div class="abs footer-col" style="left:298px;top:1109px">
      <a style="top:0" href="#">Brimwell Vacations</a>
      <a style="top:16.5px" href="#">Family Trips</a>
      <a style="top:33px" href="#">Road Trips from Texas</a>
      <a style="top:49.5px" href="#">Other Destinations</a>
    </div>
    <div class="abs footer-col" style="left:476px;top:1109px">
      <span style="top:0">hello@roamalongroad.com</span>
      <span style="top:16.5px">01 - 555 0100 200</span>
    </div>
    <a class="abs social" style="left:476px" href="#" aria-label="Photo profile"></a>
    <a class="abs social" style="left:495px" href="#" aria-label="Video channel"></a>
    <a class="abs social" style="left:514px" href="#" aria-label="Professional profile"></a>

    <div class="abs bottom-bar"></div>
  </footer>
</body>
</html>
```